Insurance Agency website design for Brellow Cover Insurance, LP

Build a website for Brellow Cover Insurance, LP which sells Homeowners, Auto, Renters, Condo, Flood, Disability, Life, Umbrella, and health insurance. We need the coolest insurance agency website out there to get quotes, contact us, or get additional information. Please list the following insurance companies we work with: Varnix, Ostle, Meridale Mutual, Quillor, Dunmarrow, KGZ, and Pellwick.

Make a design similar to https://www.fernagentry.com/

Selling personal insurance policies

```html
<!DOCTYPE html>
<html lang="en">
<head>
<meta charset="utf-8">
<title>Brellow Cover Insurance, LP</title>
<link href="https://fonts.googleapis.com/css2?family=Montserrat:wght@400;600;700;800&family=Poppins:wght@300;400;500;600&display=swap" rel="stylesheet">
<style>
:root{
  --navy:#0b2573;
  --navy-dark:#082064;
  --green:#4b9a17;
  --green-light:#7cc242;
  --pale-blue:#dde6fb;
  --pale-green:#dcebe3;
  --ink:#2a2a2a;
  --muted:#444;
  --white:#fff;
  --black:#030303;
}
*{box-sizing:border-box;margin:0;padding:0}
html,body{width:1200px;height:3525px;overflow:hidden}
body{font-family:"Poppins",sans-serif;color:var(--ink);background:var(--white);position:relative}
.abs{position:absolute}
h1,h2,h3{font-family:"Montserrat",sans-serif}

/* top bar + header */
.topbar{left:0;top:0;width:1200px;height:27px}
.topbar-green{left:650px;top:0;width:550px;height:27px;background:var(--green-light);clip-path:polygon(0 0,100% 0,100% 100%,27px 100%)}
.topbar-item{top:5px;font-size:11.5px;color:var(--white);font-weight:500;display:flex;align-items:center;gap:6px}
.header{left:0;top:27px;width:1200px;height:71px;background:var(--white)}
.logo{left:105px;top:32px;display:flex;align-items:center;gap:8px}
.logo-mark{width:20px;height:20px;background:var(--green-light)}
.logo-name{font-family:"Poppins",sans-serif;font-weight:600;font-size:14px;color:var(--navy);line-height:1.1}
.nav{top:50px;font-size:13px;font-weight:500;color:#222;letter-spacing:.2px}
.btn-quote-head{left:962px;top:38px;width:131px;height:40px;background:var(--navy);color:#fff;border-radius:3px;font-size:15px;font-weight:500;display:flex;align-items:center;justify-content:center}

/* hero */
.hero{left:0;top:98px;width:1200px;height:627px;overflow:hidden}
.hero-photo{width:100%;height:100%;background:linear-gradient(100deg,#2a4d8c 0%,#3d64a4 40%,#7a90b8 70%,#b6bfcc 100%)}
.hero-shade{inset:0;background:linear-gradient(90deg,rgba(12,45,120,.75),rgba(12,45,120,.2) 70%,rgba(12,45,120,0))}
.hero-curve{left:0;top:0;width:1200px;height:627px}
.hero-title{left:140px;top:205px;color:#fff;font-size:44px;line-height:55px;font-family:"Montserrat",sans-serif}
.hero-title b{font-weight:800}
.hero-title span{font-weight:400}
.hero-text{left:140px;top:386px;width:510px;font-size:14px;line-height:21px;color:#fff}
.hero-btn{left:140px;top:469px;width:205px;height:45px;background:var(--green-light);color:#fff;font-size:14.5px;font-weight:500;border-radius:2px;display:flex;align-items:center;justify-content:center}
.scroll-dot{left:564px;top:690px;width:70px;height:70px;border-radius:50%;background:#fff;box-shadow:0 3px 10px rgba(0,0,0,.12);display:flex;align-items:center;justify-content:center}

/* feature boxes */
.feature{top:814px;width:219px;height:212px;color:#fff;text-align:center}
.feature.navy{background:var(--navy)}
.feature.green{background:var(--green)}
.feature-icon{margin:41px auto 0;width:84px;height:84px;border-radius:50%;background:#fff;display:flex;align-items:center;justify-content:center;box-shadow:0 0 0 4px rgba(255,255,255,.25)}
.feature-label{margin-top:14px;font-size:17px;line-height:21px}

/* about */
.about-bg{left:141px;top:1115px;width:373px;height:507px;background:var(--pale-green)}
.about-frame-v{left:187px;top:1187px;width:6px;height:364px;background:var(--navy)}
.about-frame-h{left:187px;top:1545px;width:388px;height:6px;background:var(--navy)}
.about-photo{left:201px;top:1187px;width:374px;height:353px;background:linear-gradient(135deg,#8a8d92,#cfd1d3 45%,#a8a9ab)}
.about-badge{left:427px;top:1390px;width:175px;height:119px;background:var(--green);border:4px solid #fff;border-radius:8px;color:#fff;text-align:center;padding-top:10px}
.about-badge strong{display:block;font-family:"Montserrat",sans-serif;font-size:40px;line-height:44px;font-weight:700}
.about-badge span{font-size:16px;line-height:21px}
.about-title{left:643px;top:1163px;font-size:27px;font-weight:600;color:#222}
.about-copy{left:643px;top:1215px;width:412px;font-size:14.5px;line-height:21px;color:var(--muted)}
.about-copy p{margin-bottom:7px}
.btn-navy{background:var(--navy);color:#fff;border-radius:3px;font-size:14.5px;display:flex;align-items:center;justify-content:center;gap:12px;letter-spacing:.5px}
.read-more{left:643px;top:1525px;width:134px;height:41px}

/* insurance types */
.types{left:0;top:1707px;width:1200px;height:766px;background:var(--pale-blue)}
.types-title{left:144px;top:1921px;font-size:27px;font-weight:700;color:#111}
.types-copy{left:142px;top:1968px;width:420px;font-size:14.5px;line-height:21px;color:var(--muted)}
.types-copy p{margin-bottom:12px}
.view-all{left:142px;top:2212px;width:197px;height:41px}
.type-card{width:212px;height:241px;color:#fff;text-align:center}
.type-card.navy{background:var(--navy-dark)}
.type-card.green{background:var(--green)}
.type-icon{margin:26px auto 0;width:88px;height:88px;border-radius:50%;background:#fff;display:flex;align-items:center;justify-content:center;box-shadow:0 0 0 5px rgba(255,255,255,.25)}
.type-name{margin-top:20px;font-size:15px;font-weight:600;letter-spacing:.3px}
.type-desc{margin:6px auto 0;width:185px;font-size:11.5px;line-height:17px}
.type-go{width:35px;height:35px;display:flex;align-items:center;justify-content:center}
.type-go.green{background:var(--green)}
.type-go.navy{background:var(--navy-dark)}

/* partners */
.partners-title{left:0;top:2555px;width:1200px;text-align:center;font-size:27px;font-weight:700;color:#111}
.partner{top:2620px;width:161px;height:95px;background:#fff;box-shadow:0 2px 10px rgba(0,0,0,.1);display:flex;flex-direction:column;align-items:center;justify-content:center;font-family:"Poppins",sans-serif;font-weight:500;font-size:21px;color:var(--navy);letter-spacing:1px;line-height:1.15;text-align:center}
.partner small{font-size:11px;letter-spacing:0}
.arrow-btn{top:2645px;width:42px;height:42px;border-radius:50%;display:flex;align-items:center;justify-content:center}
.arrow-btn.light{background:#fff;box-shadow:0 2px 8px rgba(0,0,0,.2)}
.arrow-btn.dark{background:var(--navy)}

/* quote band */
.quote{left:0;top:2806px;width:1200px;height:304px;background:linear-gradient(90deg,#0e2c80,#1a3b90 45%,#12307f)}
.quote-photo{left:0;top:2806px;width:1200px;height:304px;background:radial-gradient(ellipse at 40% 40%,rgba(90,110,170,.35),rgba(0,0,0,0) 60%)}
.quote-title{left:0;top:2860px;width:1200px;text-align:center;font-size:27px;font-weight:700;color:#fff}
.quote-text{left:330px;top:2910px;width:540px;text-align:center;font-size:15px;line-height:21px;color:#fff}
.quote-btn{left:521px;top:3004px;width:156px;height:43px;background:var(--green);color:#fff;font-size:15px;display:flex;align-items:center;justify-content:center;gap:12px;letter-spacing:.5px}

/* footer */
.footer{left:0;top:3110px;width:1200px;height:372px;background:var(--black);color:#fff}
.foot-brand{left:142px;top:3206px;font-size:20px;font-weight:700;color:#fff}
.foot-about{left:142px;top:3260px;width:310px;font-size:12.5px;line-height:21px;color:#fff}
.foot-about u{display:block}
.foot-head{top:3208px;font-size:15px;font-weight:500;color:#fff}
.foot-head::after{content:"";display:block;width:30px;height:2px;background:#fff;margin-top:9px}
.foot-list{list-style:none;font-size:13px;color:#fff}
.quick li{height:28px;display:flex;align-items:center;gap:8px}
.social li{height:40px;display:flex;align-items:center;gap:8px}
.soc-dot{width:28px;height:28px;border-radius:50%;border:1px solid #fff}
.contact li{display:flex;gap:10px;margin-bottom:13px;line-height:19px}
.bottom-bar{left:0;top:3482px;width:1200px;height:43px;background:var(--navy);color:#fff;font-size:11.5px;display:flex;align-items:center;justify-content:center}
</style>
</head>
<body>

<!-- top bar -->
<div class="abs topbar-green"></div>
<div class="abs topbar-item" style="left:760px">
  <svg width="12" height="12" viewBox="0 0 24 24"><path fill="#fff" d="M6.6 10.8a15 15 0 006.6 6.6l2.2-2.2c.3-.3.7-.4 1-.2 1.1.4 2.3.6 3.6.6.6 0 1 .4 1 1V20c0 .6-.4 1-1 1C10.6 21 3 13.4 3 4c0-.6.4-1 1-1h3.5c.6 0 1 .4 1 1 0 1.3.2 2.5.6 3.6.1.3 0 .7-.2 1z"/></svg>
  Phone: 123-456-7890
</div>
<div class="abs" style="left:930px;top:4px;width:1px;height:19px;background:rgba(255,255,255,.6)"></div>
<div class="abs topbar-item" style="left:951px">
  <svg width="13" height="12" viewBox="0 0 24 24"><path fill="#fff" d="M2 5h20v14H2z"/><path d="M2 5l10 8 10-8" stroke="#7cc242" stroke-width="2" fill="none"/></svg>
  E-Mail: info@brellowcover.com
</div>

<!-- header -->
<header class="abs header">
</header>
<div class="abs logo">
  <div class="logo-mark"></div>
  <div class="logo-name">Brellow Cover<br>Insurance</div>
</div>
<nav>
  <div class="abs nav" style="left:309px">HOME</div>
  <div class="abs nav" style="left:391px">ABOUT US</div>
  <div class="abs nav" style="left:499px">INSURANCE
    <svg width="11" height="8" viewBox="0 0 12 8" style="margin-left:4px"><path d="M1 1l5 5 5-5" stroke="#222" stroke-width="1.6" fill="none"/></svg></div>
  <div class="abs nav" style="left:635px">MARKET PARTNERS</div>
  <div class="abs nav" style="left:803px">CONTACT</div>
</nav>
<div class="abs btn-quote-head">Get a Quote</div>

<!-- hero -->
<section class="abs hero">
  <div class="hero-photo" role="img" aria-label="Young family sitting together on the floor beside moving boxes, father holding a cardboard roof over them"></div>
  <div class="abs hero-shade"></div>
  <svg class="abs hero-curve" viewBox="0 0 1200 627" preserveAspectRatio="none">
    <path d="M0 510 L600 620 L1200 510 L1200 627 L0 627 Z" fill="#7cc242"/>
    <path d="M0 535 L600 627 L1200 535 L1200 627 L0 627 Z" fill="#ffffff"/>
  </svg>
</section>
<h1 class="abs hero-title"><b>Protect What Matters</b><br><span>Most with Trusted</span><br><b>Insurance</b></h1>
<p class="abs hero-text">At Brellow Cover Insurance, we understand how crucial it is to protect the things that matter most to you - your home, health, and family.</p>
<div class="abs hero-btn">Get Your Quote Now</div>
<div class="abs scroll-dot">
  <svg width="18" height="28" viewBox="0 0 18 28"><rect x="1.5" y="1.5" width="15" height="25" rx="7.5" fill="none" stroke="#0b2573" stroke-width="1.6"/><line x1="9" y1="7" x2="9" y2="12" stroke="#0b2573" stroke-width="1.6"/></svg>
</div>

<!-- features -->
<div class="abs feature navy" style="left:142px">
  <div class="feature-icon"><svg width="44" height="44" viewBox="0 0 44 44" fill="none" stroke="#0b2573" stroke-width="1.6"><rect x="10" y="6" width="22" height="30"/><path d="M15 13h12M15 18h12M15 23h8"/><circle cx="30" cy="30" r="6" fill="#fff"/><path d="M27 30l2 2 4-4"/></svg></div>
  <div class="feature-label">Insurance<br>Policies</div>
</div>
<div class="abs feature green" style="left:375px">
  <div class="feature-icon"><svg width="44" height="44" viewBox="0 0 44 44" fill="none" stroke="#0b2573" stroke-width="1.6"><path d="M22 35S8 26 8 17a7 7 0 0114-2 7 7 0 0114 2c0 9-14 18-14 18z"/></svg></div>
  <div class="feature-label">1000+ Happy<br>Clients</div>
</div>
<div class="abs feature navy" style="left:607px">
  <div class="feature-icon"><svg width="44" height="44" viewBox="0 0 44 44" fill="none" stroke="#0b2573" stroke-width="1.6"><path d="M11 22a11 11 0 0122 0"/><rect x="8" y="21" width="6" height="9" rx="2"/><rect x="30" y="21" width="6" height="9" rx="2"/><path d="M33 30c0 4-4 6-9 6"/><path d="M10 40c2-5 7-7 12-7s10 2 12 7"/></svg></div>
  <div class="feature-label">Professional<br>Support</div>
</div>
<div class="abs feature green" style="left:840px">
  <div class="feature-icon"><svg width="44" height="44" viewBox="0 0 44 44" fill="none" stroke="#0b2573" stroke-width="1.6"><circle cx="22" cy="22" r="6"/><circle cx="22" cy="22" r="12" stroke-dasharray="5 3"/><circle cx="22" cy="22" r="16"/></svg></div>
  <div class="feature-label">Free Lifetime<br>Updates</div>
</div>

<!-- about -->
<div class="abs about-bg"></div>
<div class="abs about-frame-v"></div>
<div class="abs about-frame-h"></div>
<div class="abs about-photo" role="img" aria-label="Insurance advisor meeting with an older couple at an office table"></div>
<div class="abs about-badge"><strong>50+</strong><span>Skilled<br>Professionals</span></div>
<h2 class="abs about-title">BRELLOW COVER INSURANCE</h2>
<div class="abs about-copy">
  <p>Brellow Cover Insurance is a full-service, independent insurance agency with over three decades of experience in delivering comprehensive insurance solutions to individuals.</p>
  <p>We proudly offer a diverse portfolio of products from more than 20 of the most reputable and financially secure companies in the industry. Our dedicated team of over 50 skilled professionals is committed to customizing these products and services to meet the unique needs of each client.</p>
  <p>At Brellow Cover Insurance, our experts are focused on addressing the individual needs of our clients, ensuring exceptional service and support at every step.</p>
</div>
<div class="abs btn-navy read-more">Read More
  <svg width="10" height="10" viewBox="0 0 10 10"><path d="M2 8l6-6M3 2h5v5" stroke="#fff" stroke-width="1.2" fill="none"/></svg></div>

<!-- insurance types -->
<section class="abs types"></section>
<h2 class="abs types-title">INSURANCE TYPES</h2>
<div class="abs types-copy">
  <p>Lorem ipsum dolor sit amet, consectetuer adipiscing elit, sed diam nonummy nibh euismod tincidunt ut laoreet dolore magna aliquam erat volutpat.</p>
  <p>Lorem ipsum dolor sit amet, consectetuer adipiscing elit, sed diam nonummy nibh euismod tincidunt ut laoreet dolore magna aliquam erat volutpat. Ut wisi enim ad minim veniam, quis nostrud exerci tation ullamcorper suscipit lobortis nisl ut aliquip ex ea commodo consequat. Duis autem vel eum iriure dolor in hendrerit in vulputate velit esse molestie consequat.</p>
</div>
<div class="abs btn-navy view-all">View All Insurance
  <svg width="10" height="10" viewBox="0 0 10 10"><path d="M2 8l6-6M3 2h5v5" stroke="#fff" stroke-width="1.2" fill="none"/></svg></div>

<div class="abs type-card navy" style="left:613px;top:1796px">
  <div class="type-icon"><svg width="48" height="48" viewBox="0 0 48 48" fill="none" stroke="#082064" stroke-width="1.7"><path d="M6 22L24 8l18 14M11 18v22h26V18"/><circle cx="24" cy="28" r="6"/></svg></div>
  <div class="type-name">HOMEOWNERS</div>
  <div class="type-desc">Lorem Ipsum is simply dummy text of the printing typesetting industry Lorem Ipsum has</div>
</div>
<div class="abs type-go green" style="left:701px;top:2020px"><svg width="10" height="10" viewBox="0 0 10 10"><path d="M2 8l6-6M3 2h5v5" stroke="#fff" stroke-width="1.2" fill="none"/></svg></div>

<div class="abs type-card green" style="left:848px;top:1845px">
  <div class="type-icon"><svg width="48" height="48" viewBox="0 0 48 48" fill="none" stroke="#082064" stroke-width="1.7"><path d="M6 30v-6l5-9h18l5 9v6z"/><circle cx="13" cy="32" r="3"/><circle cx="29" cy="32" r="3"/><path d="M34 18l8 3v6c0 5-4 8-8 9-4-1-8-4-8-9v-6z" fill="#fff"/><path d="M31 27l2 2 4-4"/></svg></div>
  <div class="type-name">AUTO</div>
  <div class="type-desc">Lorem Ipsum is simply dummy text of the printing typesetting industry Lorem Ipsum has</div>
</div>
<div class="abs type-go navy" style="left:936px;top:2069px"><svg width="10" height="10" viewBox="0 0 10 10"><path d="M2 8l6-6M3 2h5v5" stroke="#fff" stroke-width="1.2" fill="none"/></svg></div>

<div class="abs type-card green" style="left:612px;top:2078px">
  <div class="type-icon"><svg width="48" height="48" viewBox="0 0 48 48" fill="none" stroke="#082064" stroke-width="1.7"><path d="M10 22L24 10l14 12M14 19v13h20V19"/><path d="M8 40c4-4 8-6 16-6s12 2 16 6"/><path d="M24 22v6M21 25h6"/></svg></div>
  <div class="type-name">RENTERS</div>
  <div class="type-desc">Lorem Ipsum is simply dummy text of the printing typesetting industry Lorem Ipsum has</div>
</div>
<div class="abs type-go navy" style="left:700px;top:2302px"><svg width="10" height="10" viewBox="0 0 10 10"><path d="M2 8l6-6M3 2h5v5" stroke="#fff" stroke-width="1.2" fill="none"/></svg></div>

<div class="abs type-card navy" style="left:848px;top:2127px">
  <div class="type-icon"><svg width="48" height="48" viewBox="0 0 48 48" fill="none" stroke="#082064" stroke-width="1.7"><circle cx="22" cy="9" r="3"/><path d="M22 13v12h10l4 10"/><path d="M18 22a9 9 0 1012 11"/></svg></div>
  <div class="type-name">DISABILITY</div>
  <div class="type-desc">Lorem Ipsum is simply dummy text of the printing typesetting industry Lorem Ipsum has</div>
</div>
<div class="abs type-go green" style="left:936px;top:2351px"><svg width="10" height="10" viewBox="0 0 10 10"><path d="M2 8l6-6M3 2h5v5" stroke="#fff" stroke-width="1.2" fill="none"/></svg></div>

<!-- partners -->
<h2 class="abs partners-title">OUR PARTNERS</h2>
<div class="abs arrow-btn light" style="left:141px"><svg width="14" height="12" viewBox="0 0 14 12"><path d="M13 6H2M6 1L1 6l5 5" stroke="#111" stroke-width="1.6" fill="none"/></svg></div>
<div class="abs partner" style="left:245px">VARNIX</div>
<div class="abs partner" style="left:428px">OSTLE</div>
<div class="abs partner" style="left:611px">MERIDALE<br>MUTUAL<small>a Corvane company</small></div>
<div class="abs partner" style="left:795px">DUNMARROW</div>
<div class="abs arrow-btn dark" style="left:1016px"><svg width="14" height="12" viewBox="0 0 14 12"><path d="M1 6h11M8 1l5 5-5 5" stroke="#fff" stroke-width="1.6" fill="none"/></svg></div>

<!-- quote -->
<section class="abs quote"></section>
<div class="abs quote-photo" role="img" aria-label="Smiling couple reviewing paperwork, tinted deep blue"></div>
<h2 class="abs quote-title">GET A QUOTE TODAY</h2>
<p class="abs quote-text">Lorem ipsum dolor sit amet, consectetuer adipiscing elit, sed diam nonummy nibh euismod tincidunt ut laoreet dolore magna aliquam erat volutpat. Ut wisi enim ad minim veniam.</p>
<div class="abs quote-btn">Get a Quote
  <svg width="10" height="10" viewBox="0 0 10 10"><path d="M2 8l6-6M3 2h5v5" stroke="#fff" stroke-width="1.2" fill="none"/></svg></div>

<!-- footer -->
<footer class="abs footer"></footer>
<h3 class="abs foot-brand">BRELLOW COVER INSURANCE</h3>
<p class="abs foot-about">Lorem ipsum dolor sit amet, consectetuer adipiscing elit, sed diam nonummy nibh euismod tincidunt utted is laoreet dolore magna aliquam erat volutpat. Ut wisi enim ad minim veniam.<u>Read More</u></p>

<div class="abs foot-head" style="left:513px">Quick Links</div>
<ul class="abs foot-list quick" style="left:513px;top:3254px">
  <li>»&nbsp;Home</li><li>»&nbsp;About Us</li><li>»&nbsp;Insurance Types</li><li>»&nbsp;Contact Us</li><li>»&nbsp;Get a Quote</li>
</ul>

<div class="abs foot-head" style="left:691px">Follow Us</div>
<ul class="abs foot-list social" style="left:691px;top:3250px">
  <li><span class="soc-dot"></span>Socialia</li>
  <li><span class="soc-dot"></span>Streamly</li>
  <li><span class="soc-dot"></span>Picboard</li>
  <li><span class="soc-dot"></span>Chirper</li>
</ul>

<div class="abs foot-head" style="left:829px">Contact Details</div>
<ul class="abs foot-list contact" style="left:829px;top:3259px">
  <li><svg width="12" height="16" viewBox="0 0 12 16" style="margin-top:2px"><path fill="#fff" d="M6 0a6 6 0 00-6 6c0 4.5 6 10 6 10s6-5.5 6-10a6 6 0 00-6-6zm0 8.5A2.5 2.5 0 116 3.5a2.5 2.5 0 010 5z"/></svg><span>Address<br>123 Building Name,<br>City Name, State XY-123456.</span></li>
  <li><svg width="13" height="13" viewBox="0 0 24 24" style="margin-top:3px"><path fill="#fff" d="M6.6 10.8a15 15 0 006.6 6.6l2.2-2.2c.3-.3.7-.4 1-.2 1.1.4 2.3.6 3.6.6.6 0 1 .4 1 1V20c0 .6-.4 1-1 1C10.6 21 3 13.4 3 4c0-.6.4-1 1-1h3.5c.6 0 1 .4 1 1 0 1.3.2 2.5.6 3.6.1.3 0 .7-.2 1z"/></svg><span>Phone<br>(555) 454-0186</span></li>
  <li><svg width="13" height="11" viewBox="0 0 24 20" style="margin-top:4px"><path fill="#fff" d="M0 2h24v16H0z"/><path d="M0 2l12 9 12-9" stroke="#000" stroke-width="2" fill="none"/></svg><span>Email<br>info@BrellowCoverInsurance.com</span></li>
</ul>

<div class="abs bottom-bar">Copyright © 2025 Brellow Cover Insurance. All Rights Reserved.</div>

</body>
</html>
```